Seeking a new website design for electrical contracting company

Brisket & Vane electrical contracting needs a new website for brisket-vane.example

We are looking for modern and something real cool with motion for a landing page. we have some cool images from our photo shoot. maybe even 3d motion our existing logo. we would like something we can edit with news and events and update a past project page. Also allow to take payment
stock images at
https://lorapellwinphotos.picvault-demo.example/Brisket-and-Vane

Target Market(s)

construction , home owners , business owners,

Industry/Entity Type

construction , electrical

Coding

Number of Pages Required

5+ page

Font styles to use
Serif
Sans Serif

Colors
0054AA
0677BA
7BADD7
CADEEF
E8F1F8
0094D4
00A9DD
6FCCEA
C7EBF8
E9F6FB
FFF300
FFF600
FEFA6F
FFFEC7
FFFEE8

Requirements
Must have
• excitement, motion, selling professionalism,

```html
<!DOCTYPE html>
<html lang="en">
<head>
<meta charset="utf-8">
<title>Brisket &amp; Vane — Electrical Contractors</title>
<link href="https://fonts.googleapis.com/css2?family=Bebas+Neue&family=Outfit:wght@400;500;600;700&display=swap" rel="stylesheet">
<style>
:root{
  --blue:#0054AA;
  --blue-mid:#0677BA;
  --blue-soft:#7BADD7;
  --yellow:#FFF300;
  --black:#000000;
  --ink:#111111;
  --grey:#F2F2F2;
  --line:#CFCFCF;
  --muted:#777777;
  --white:#FFFFFF;
}
*{margin:0;padding:0;box-sizing:border-box}
html,body{width:1200px;height:5041px;overflow:hidden}
body{position:relative;background:var(--white);font-family:"Outfit",sans-serif;color:var(--ink)}
.abs{position:absolute}
.display{font-family:"Bebas Neue",sans-serif;font-weight:400;line-height:1;letter-spacing:.5px}
.tag{position:absolute;background:var(--yellow);color:var(--black);font-size:11px;font-weight:500;padding:3px 8px;border-radius:2px;line-height:1.2}
.btn{position:absolute;background:var(--blue);color:var(--white);font-size:11px;font-weight:600;letter-spacing:.4px;display:flex;align-items:center;justify-content:center;gap:5px;border-radius:3px;text-transform:uppercase}
.btn::after{content:"";border-left:5px solid currentColor;border-top:4px solid transparent;border-bottom:4px solid transparent}
.btn.yellow{background:var(--yellow);color:var(--black)}
.copy{font-size:13px;line-height:1.45}
.ruled{border-left:1.5px solid #333;padding-left:16px}
.photo{position:absolute;overflow:hidden}

/* header */
.site-header{position:absolute;left:0;top:0;width:1200px;height:92px;background:var(--black)}
.brand{position:absolute;display:flex;align-items:center;gap:10px;font-weight:700;font-size:21px}
.brand-mark{width:34px;height:34px;background:var(--yellow);border-radius:50%}
.site-header .brand{left:70px;top:28px;color:var(--white)}
.nav{position:absolute;top:33px;left:434px;display:flex;gap:36px;color:var(--white);font-size:15px}
.nav .active{font-weight:700}
.book{left:1012px;top:25px;width:116px;height:36px}

/* hero */
.hero-photo{left:72px;top:115px;width:1055px;height:421px;border-radius:22px;background:linear-gradient(120deg,#3b4652 0%,#7b7f86 35%,#b9b2a6 55%,#536171 100%)}
.play{position:absolute;left:534px;top:299px}
.hero-title{left:72px;top:610px;font-size:44px;color:var(--black)}
.hero-copy{left:757px;top:588px;width:400px;height:82px;padding-top:14px;font-size:12.5px}

/* about */
.about{position:absolute;left:0;top:820px;width:1200px;height:654px;background:var(--black)}
.about-photo{left:68px;top:855px;width:449px;height:554px;border-radius:22px;background:linear-gradient(160deg,#d9d6cf 0%,#8e8a83 40%,#3d4148 100%)}
.exp-card{position:absolute;left:382px;top:1243px;width:225px;height:166px;background:var(--blue);border-radius:22px;color:var(--white);font-size:42px;padding:42px 26px}
.about-title{left:642px;top:1024px;font-size:54px;line-height:1.12;color:var(--white)}
.about-copy{left:652px;top:1153px;width:400px;color:var(--white);font-size:12.5px;border-left:1.5px solid var(--white);padding-left:13px}

/* tapes */
.tape{position:absolute;left:0;width:1200px}
.tape text{font-family:"Outfit",sans-serif;font-weight:700;font-size:17px;fill:var(--white);white-space:pre}

/* services */
.section-title{position:absolute;font-size:50px;color:var(--black)}
.services-copy{left:777px;top:1558px;width:390px;font-size:12.5px;height:58px}
.services-panel{position:absolute;left:47px;top:1646px;width:1108px;height:462px;background:var(--grey);border-radius:22px;overflow:hidden}
.service-tab{position:absolute;left:0;top:0;width:72px;height:462px;background:var(--black);color:var(--white)}
.service-tab .num{position:absolute;top:22px;left:16px;font-size:48px}
.vlabel{position:absolute;transform:rotate(-90deg);transform-origin:left top;white-space:nowrap;font-size:24px}
.service-tab .vlabel{left:22px;top:400px}
.service-photo{left:96px;top:24px;width:612px;height:262px;border-radius:20px;background:linear-gradient(110deg,#6c7d62 0%,#b9c1b8 40%,#eef0f1 60%,#8a9096 100%)}
.service-icon{position:absolute;left:131px;top:243px;width:82px;height:82px;background:var(--blue);border-radius:14px;display:flex;align-items:center;justify-content:center}
.service-text{position:absolute;left:96px;top:342px;width:612px;font-size:12.5px;line-height:1.45}
.service-col{position:absolute;top:0;width:92px;height:462px;border-left:1px solid var(--line)}
.service-col .num{position:absolute;top:44px;left:0;width:92px;text-align:center;font-size:46px;color:var(--ink)}
.service-col .vlabel{left:34px;top:430px;font-size:24px;color:var(--ink)}

/* featured */
.featured-copy{left:59px;top:2284px;width:390px;font-size:12.5px}
.team-photo{left:59px;top:2366px;width:556px;height:234px;border-radius:20px;background:linear-gradient(90deg,#4a4038 0%,#8a7b6c 30%,#6e6358 60%,#3a332e 100%)}
.stat{position:absolute;width:200px;text-align:center}
.stat svg{display:block;margin:0 auto}
.stat .value{font-size:52px;margin-top:8px;color:var(--ink)}
.stat .label{font-size:14px;color:var(--muted);line-height:1.9;margin-top:4px}

/* dark band */
.dark{position:absolute;left:0;top:2707px;width:1200px;height:984px;background:var(--black)}
.center{left:0;width:1200px;text-align:center}
.center-tag{left:50%;transform:translateX(-50%)}
.review{position:absolute;top:2906px;width:318px;color:var(--white)}
.quote{font-family:Georgia,serif;font-weight:700;font-size:74px;line-height:.7;color:var(--blue);height:40px}
.review p{font-size:12.5px;line-height:1.45;margin-top:14px;height:150px}
.reviewer{display:flex;align-items:center;gap:14px;border-bottom:1px solid #444;padding-bottom:12px;margin-top:14px;font-size:13px}
.avatar{width:60px;height:60px;border-radius:50%;background:linear-gradient(135deg,#8d8d8d,#3a3a3a);flex:none;border:2px solid #555}
.dots{left:572px;top:3196px;display:flex;gap:4px}
.dots span{width:7px;height:7px;border-radius:50%;background:var(--white)}
.dots span.off{background:transparent;border:1px solid var(--white)}

/* blog */
.blog-rule{left:47px;top:3402px;width:1108px;height:1px;background:#555}
.blog-photo{border-radius:20px}
.blog-title{position:absolute;font-size:31px;line-height:1.2}
.blog-copy{position:absolute;font-size:12.5px;line-height:1.45}

/* contact */
.contact-band{position:absolute;left:0;top:4511px;width:1200px;height:180px;background:var(--black)}
.contact{position:absolute;left:72px;top:4231px;width:1053px;height:458px;border-radius:22px;overflow:hidden;background:var(--blue)}
.contact-photo{left:415px;top:0;width:638px;height:458px;background:linear-gradient(180deg,#d8d2c6 0%,#8a6e58 40%,#b8b3aa 70%,#9a9892 100%)}
.contact-title{left:40px;top:60px;font-size:46px;color:var(--white)}
.contact-copy{left:40px;top:126px;width:320px;color:var(--white);font-size:12.5px}
.field{position:absolute;left:40px;width:322px;background:var(--white);border-radius:5px;font-size:10px;color:#999;padding:9px 12px}
.submit{left:135px;top:380px;width:106px;height:35px}

/* footer */
.site-footer .brand{left:59px;top:4796px;color:var(--blue);font-size:25px}
.site-footer .brand-mark{width:40px;height:40px;background:var(--blue)}
.social{position:absolute;top:4863px;left:59px;display:flex;gap:22px}
.social span{width:26px;height:26px;border-radius:50%;background:var(--blue)}
.foot-col{position:absolute;top:4790px;font-size:12.5px;line-height:27px}
.foot-col h4{color:var(--blue);font-size:14px;font-weight:600;margin-bottom:2px}
.foot-rule{left:59px;top:4973px;width:1132px;height:1px;background:#bbb}
.legal{position:absolute;top:4998px;font-size:11px;color:#444}
</style>
</head>
<body>

<!-- Header -->
<header class="site-header">
  <div class="brand"><span class="brand-mark"></span>Brisket &amp; Vane</div>
  <nav class="nav">
    <span class="active">Home</span><span>Service</span><span>About</span><span>Project</span><span>Contact</span><span>Blog</span>
  </nav>
  <a class="btn book">Book now</a>
</header>

<!-- Hero -->
<div class="photo hero-photo" role="img" aria-label="Close-up of an electrician's tool belt filled with pliers and screwdrivers"></div>
<svg class="play" width="40" height="40" viewBox="0 0 40 40" aria-hidden="true">
  <circle cx="20" cy="20" r="17" fill="none" stroke="#fff" stroke-width="2.5"/>
  <path d="M16 12 L28 20 L16 28 Z" fill="#fff"/>
</svg>
<span class="tag" style="left:74px;top:567px">100% Secure &amp; Reliable Electricien</span>
<h1 class="abs display hero-title">Your Trusted Electrical Services</h1>
<p class="abs copy hero-copy ruled">Fames metus cras vestibulum torquent blandit in ultrices fermentum urna per quisque egestas feugiat conubia posuere aliquam molestie montes tristique</p>
<a class="btn" style="left:72px;top:669px;width:145px;height:37px">Discover more</a>

<!-- About -->
<section class="about"></section>
<svg class="tape" style="top:740px" width="1200" height="140" viewBox="0 740 1200 140">
  <g transform="translate(0,838) rotate(-0.95)"><rect x="-30" y="-17" width="1280" height="34" fill="#FFF300"/></g>
  <g transform="translate(0,786) rotate(2.96)">
    <rect x="-30" y="-19" width="1280" height="38" fill="#0054AA"/>
    <text x="-40" y="6">BRISKET &amp; VANE    ◆    BRISKET &amp; VANE    ◆    BRISKET &amp; VANE    ◆    BRISKET &amp; VANE    ◆    BRISKET &amp; VANE    ◆    BRISKET &amp; VANE    ◆    BRISKET</text>
  </g>
</svg>
<div class="photo about-photo" role="img" aria-label="Smiling electrician in sunglasses driving a company van"></div>
<div class="exp-card display">10+ Year<br>Experience</div>
<span class="tag" style="left:642px;top:979px">About us</span>
<h2 class="abs display about-title">Affordable Electrican<br>Repair Services</h2>
<p class="abs copy about-copy">Fames metus cras vestibulum torquent blandit in ultrices fermentum urna per quisque egestas feugiat conubia posuere aliquam molestie montes tristique</p>
<a class="btn" style="left:642px;top:1241px;width:141px;height:35px">Contact now</a>

<!-- Services -->
<h2 class="display section-title" style="left:47px;top:1564px">Our Services</h2>
<p class="abs copy services-copy ruled">Fames metus cras vestibulum torquent blandit in ultrices fermentum urna per quisque egestas feugiat conubia posuere aliquam molestie montes tristique</p>
<div class="services-panel">
  <div class="service-tab">
    <span class="num display">01</span>
    <span class="vlabel display">House Maintenance</span>
  </div>
  <div class="photo service-photo" role="img" aria-label="Two white company service vans parked side by side"></div>
  <div class="service-icon">
    <svg width="40" height="40" viewBox="0 0 40 40" fill="none" stroke="#fff" stroke-width="2" aria-hidden="true">
      <path d="M8 8 H32 L35 26 H5 Z"/><path d="M7 14 H33 M6 20 H34 M15 8 L13 26 M25 8 L27 26"/><path d="M20 26 V33 M13 33 H27"/>
    </svg>
  </div>
  <p class="service-text">Fames metus cras vestibulum torquent blandit in ultrices fermentum urna per quisque egestas feugiat conubia posuere aliquam molestie montes tristique<br>Fames metus cras vestibulum torquent blandit in ultrices fermentum urna per quisque egestas feugiat conubia posuere aliquam molestie montes tristique</p>
  <div class="service-col" style="left:740px"><span class="num display">02</span><span class="vlabel display">Emergency Services</span></div>
  <div class="service-col" style="left:832px"><span class="num display">03</span><span class="vlabel display">Electric Panel Repair</span></div>
  <div class="service-col" style="left:924px"><span class="num display">04</span><span class="vlabel display">Air Conditioning</span></div>
  <div class="service-col" style="left:1016px"><span class="num display">05</span><span class="vlabel display">Repairs &amp; Rewiring</span></div>
</div>

<!-- Featured works -->
<h2 class="display section-title" style="left:59px;top:2216px">Featured Works</h2>
<p class="abs copy featured-copy ruled">Fames metus cras vestibulum torquent blandit in ultrices fermentum urna per quisque egestas feugiat conubia posuere aliquam molestie montes tristique</p>
<div class="photo team-photo" role="img" aria-label="Five electricians in matching polo shirts standing with arms crossed"></div>
<a class="btn" style="left:59px;top:2620px;width:111px;height:33px">View more</a>

<div class="stat" style="left:646px;top:2228px">
  <svg width="56" height="64" viewBox="0 0 56 64" fill="none" stroke="#0054AA" stroke-width="2.5" aria-hidden="true"><rect x="10" y="4" width="36" height="56" rx="3"/><rect x="18" y="16" width="20" height="20"/><path d="M4 14 H10 M4 24 H10 M4 34 H10 M46 14 H52 M46 24 H52 M46 34 H52 M20 46 H36 M20 52 H30"/></svg>
  <div class="value display">2501</div><div class="label">Satisfied<br>Clients</div>
</div>
<div class="stat" style="left:912px;top:2228px">
  <svg width="56" height="64" viewBox="0 0 56 64" fill="none" stroke="#0054AA" stroke-width="2.5" aria-hidden="true"><rect x="10" y="14" width="10" height="34" rx="3"/><rect x="36" y="14" width="10" height="34" rx="3"/><path d="M15 4 V14 M15 48 V60 M41 4 V14 M41 48 V60 M10 26 H20 M10 36 H20 M36 26 H46 M36 36 H46"/></svg>
  <div class="value display">30</div><div class="label">Years Of<br>Experience</div>
</div>
<div class="stat" style="left:646px;top:2468px">
  <svg width="56" height="64" viewBox="0 0 56 64" fill="none" stroke="#0054AA" stroke-width="2.5" aria-hidden="true"><rect x="12" y="8" width="32" height="52" rx="5"/><rect x="18" y="14" width="20" height="12"/><circle cx="28" cy="42" r="8"/><path d="M28 42 L32 37 M4 20 V54 M4 54 H12"/></svg>
  <div class="value display">4500</div><div class="label">Project<br>Complete</div>
</div>
<div class="stat" style="left:912px;top:2468px">
  <svg width="56" height="64" viewBox="0 0 56 64" fill="none" stroke="#0054AA" stroke-width="2.5" aria-hidden="true"><path d="M8 8 H38 V26 H8 Z M38 14 H48 M48 12 V20 M18 26 L14 48 H30 L28 26 M14 48 V58 H30 V48"/><path d="M14 14 H30 M14 20 H30"/></svg>
  <div class="value display">3020</div><div class="label">Awards Wining<br>Company</div>
</div>

<!-- Testimonials + blog dark area -->
<section class="dark"></section>
<span class="tag center-tag" style="top:2762px">Testimonials</span>
<h2 class="abs display center" style="top:2822px;font-size:48px;color:#fff">Real Stories, Real Safisfaction</h2>

<article class="review" style="left:59px">
  <div class="quote">““</div>
  <p>Fames metus cras vestibulum torquent blandit in ultrices fermentum urna per quisque egestas feugiat conubia posuere aliquam molestie montes tristiqueFames metus cras vestibulum torquent blandit in ultrices fermentum urna per quisque egestas feugiat conubia posuere aliquam molestie montes tristique</p>
  <div class="reviewer"><span class="avatar" role="img" aria-label="Customer portrait"></span>Owen Calder, New York</div>
</article>
<article class="review" style="left:426px">
  <div class="quote">““</div>
  <p>Fames metus cras vestibulum torquent blandit in ultrices fermentum urna per quisque egestas feugiat conubia posuere aliquam molestie montes tristiqueFames metus cras vestibulum torquent blandit in ultrices fermentum urna per quisque egestas feugiat conubia posuere aliquam molestie montes tristique</p>
  <div class="reviewer"><span class="avatar" role="img" aria-label="Customer portrait"></span>Rhys Morrow, New York</div>
</article>
<article class="review" style="left:793px">
  <div class="quote">““</div>
  <p>Fames metus cras vestibulum torquent blandit in ultrices fermentum urna per quisque egestas feugiat conubia posuere aliquam molestie montes tristiqueFames metus cras vestibulum torquent blandit in ultrices fermentum urna per quisque egestas feugiat conubia posuere aliquam molestie montes tristique</p>
  <div class="reviewer"><span class="avatar" role="img" aria-label="Customer portrait"></span>Theo Banning, New York</div>
</article>
<div class="abs dots"><span class="off"></span><span></span><span></span></div>

<!-- Blog -->
<span class="tag center-tag" style="top:3296px">Blogs</span>
<h2 class="abs display center" style="top:3337px;font-size:50px;color:#fff">Expert Tips, Safety Advice &amp; Industry News</h2>
<div class="abs blog-rule"></div>

<div class="photo blog-photo" style="left:55px;top:3425px;width:337px;height:433px;background:linear-gradient(180deg,#8a4a36 0%,#a9573f 35%,#4d5966 70%,#2f3a46 100%)" role="img" aria-label="Four electricians standing in front of a brick building and vans"></div>
<h3 class="display blog-title" style="left:55px;top:3876px;color:#000">Expert Tips, Safety Advice &amp;<br>Industry News</h3>
<p class="blog-copy" style="left:55px;top:3964px;width:300px">Is your wiring outdated? Here's how to tell before it becomes a safety hazard.</p>

<h3 class="display blog-title" style="left:434px;top:3430px;color:#fff">The Importance Of Hiring A<br>Licensed Electrician</h3>
<p class="blog-copy" style="left:434px;top:3517px;width:320px;color:#fff">DIY may be tempting, but here's why certified pros are worth it—especially when safety is on the line.</p>
<div class="photo blog-photo" style="left:434px;top:3583px;width:339px;height:435px;background:linear-gradient(170deg,#b6c4cf 0%,#eef0f2 35%,#c9ccd0 60%,#4b4f55 100%)" role="img" aria-label="White company van parked on a street"></div>

<div class="photo blog-photo" style="left:814px;top:3425px;width:339px;height:433px;background:linear-gradient(160deg,#b7b9bb 0%,#cfd0d0 40%,#8f8f8f 100%)" role="img" aria-label="Electrician in a grey shirt pointing outward"></div>
<h3 class="display blog-title" style="left:814px;top:3876px;color:#000">Understanding Your<br>Electrical Panel: A Quick<br>Homeowner's Guide</h3>
<p class="blog-copy" style="left:814px;top:3998px;width:310px">Demystify that breaker box and learn how to spot issues before they escalate.</p>

<a class="btn" style="left:536px;top:4059px;width:135px;height:35px">Learn more</a>

<svg class="tape" style="top:4110px" width="1200" height="120" viewBox="0 4110 1200 120">
  <g transform="translate(0,4200) rotate(-0.8)"><rect x="-30" y="-16" width="1280" height="32" fill="#FFF300"/></g>
  <g transform="translate(0,4137) rotate(1.9)">
    <rect x="-30" y="-18" width="1280" height="36" fill="#0054AA"/>
    <text x="-40" y="6">BRISKET &amp; VANE    ◆    BRISKET &amp; VANE    ◆    BRISKET &amp; VANE    ◆    BRISKET &amp; VANE    ◆    BRISKET &amp; VANE    ◆    BRISKET &amp; VANE    ◆    BRISKET</text>
  </g>
</svg>

<!-- Contact -->
<div class="contact-band"></div>
<section class="contact">
  <h2 class="abs display contact-title">Get To Touch</h2>
  <p class="abs copy contact-copy">Demystify that breaker box and learn how to spot issues before they escalate.</p>
  <div class="field" style="top:181px;height:34px">Name</div>
  <div class="field" style="top:224px;height:35px">Email address</div>
  <div class="field" style="top:267px;height:92px">Message</div>
  <a class="btn yellow submit">Submit</a>
  <div class="photo contact-photo" role="img" aria-label="Crew of electricians standing beside a fleet of white vans outside a brick building"></div>
</section>

<!-- Footer -->
<footer class="site-footer">
  <div class="brand"><span class="brand-mark"></span>Brisket &amp; Vane</div>
  <div class="social" aria-label="Social links"><span></span><span></span><span></span><span></span></div>
  <div class="foot-col" style="left:415px"><h4>Quick Link</h4>Home<br>About<br>Service<br>Testimonial</div>
  <div class="foot-col" style="left:658px"><h4>Service</h4>Residential<br>Commercial<br>House Maintenance<br>Electric Panel Repair</div>
  <div class="foot-col" style="left:902px"><h4>Contact Us</h4>(555) 014-2290<br>office@brisket-vane.example<br>48 Harlow Lane, Millbrook, Nevada<br>Help &amp; Contact</div>
  <div class="abs foot-rule"></div>
  <p class="legal" style="left:59px">All Rights Reserved © 2025 Brisket &amp; Vane Electrical Contractors</p>
  <p class="legal" style="left:934px">Privacy Policy</p>
  <p class="legal" style="left:1041px">Terms &amp; Condition</p>
</footer>

</body>
</html>
```